New Business Card for Web Design/Internet Marketing Company

Looking for a great looking new business card. We are a 10 year old web design, internet marketing and website management company that works mostly with small businesses.

Our new card needs to better match the colors and style of our website, be bold, extremely usable and slightly edgy.

Target Market(s)

Small/Medium businesses that have websites

Industry/Entity Type

Internet

Requirements
Must have
• Front and back design, full color, rounded corners please

Must use the colors/style of our website (JPG provided)

INFO FOR CARDS (as readable as possible please)
Mark Lenner
President/CEO
mark@trelvanmedia.example
Phone: 520-381-7459
Toll Free: 866-381-7459
Address: 4315 W. Calloway Ave. Ste. 140, Tucson, AZ 85792

THINGS I WANT TO PROMOTE (if there is room):
1. Our Website - www.trelvanmedia.example

2. Social Media
Twitter: @trelvanmedia
Facebook: www.facebook.com/trelvanmedia

3. Our Services
Web Design
Internet Marketing
Website Management

```html
<!DOCTYPE html>
<html lang="en">
<head>
<meta charset="utf-8">
<title>Trelvan Media – Business Card</title>
<link href="https://fonts.googleapis.com/css2?family=Open+Sans:ital,wght@0,400;0,600;0,700;1,700&display=swap" rel="stylesheet">
<style>
  :root {
    --stage: #1e1e20;
    --blue-deep: #0a2f6e;
    --blue-mid: #1252a8;
    --blue-bright: #1e90d6;
    --accent-blue: #1a8fd0;
    --orange: #f4a51c;
    --white: #ffffff;
    --grey-text: #7a7a7a;
    --grey-dark: #5e5e5e;
  }
  * { margin: 0; padding: 0; box-sizing: border-box; }
  html, body { width: 1200px; height: 500px; overflow: hidden; }
  body {
    position: relative;
    background: var(--stage);
    font-family: "Open Sans", sans-serif;
  }
  .card {
    position: absolute;
    top: 110px;
    width: 492px;
    height: 278px;
    border-radius: 22px;
    overflow: hidden;
  }

  /* Front side */
  .card--front {
    left: 100px;
    background: radial-gradient(ellipse at 45% 35%, var(--blue-bright) 0%, var(--blue-mid) 45%, var(--blue-deep) 100%);
  }
  .front-backdrop { position: absolute; inset: 0; }
  .front-brand {
    position: absolute;
    left: 0; right: 0; top: 98px;
    display: flex; align-items: center; justify-content: center; gap: 8px;
  }
  .brand-dot {
    width: 16px; height: 16px; border-radius: 50%;
    background: var(--accent-blue);
    border: 2px solid var(--white);
  }
  .brand-name {
    font-weight: 700; font-size: 22px; color: var(--orange);
  }
  .front-contact {
    position: absolute; left: 21px; top: 197px;
    font-style: normal;
    color: var(--white); font-size: 14px; line-height: 22px;
  }
  .front-divider {
    position: absolute; left: 216px; top: 198px;
    width: 2px; height: 62px; background: var(--white);
  }
  .front-social {
    position: absolute; left: 233px; top: 197px;
    list-style: none;
    color: var(--white); font-size: 14px; line-height: 22px;
  }
  .front-social li { display: flex; align-items: center; gap: 7px; }
  .social-mark {
    width: 16px; height: 16px; border-radius: 3px; background: var(--orange);
  }

  /* Back side */
  .card--back { left: 607px; background: var(--white); }
  .back-swoosh { position: absolute; inset: 0; }
  .back-tab {
    position: absolute; left: 0; top: 30px;
    width: 15px; height: 42px; background: var(--accent-blue);
  }
  .back-brand {
    position: absolute; left: 26px; top: 44px;
    display: flex; align-items: center; gap: 9px;
  }
  .back-brand .brand-name { font-size: 28px; }
  .back-brand .brand-dot { width: 22px; height: 22px; border: none; }
  .services { position: absolute; left: 21px; top: 170px; }
  .services-title {
    font-weight: 700; font-style: italic; font-size: 16px; color: var(--orange);
    margin-bottom: 2px;
  }
  .services-title span { color: var(--accent-blue); }
  .services ul { list-style: none; }
  .services li {
    display: flex; align-items: center; gap: 6px;
    font-size: 16px; line-height: 22px; color: var(--grey-text);
  }
  .service-dot {
    width: 12px; height: 12px; border-radius: 50%; background: var(--accent-blue);
  }
  .person {
    position: absolute; right: 22px; top: 140px; text-align: right;
  }
  .person-name {
    font-size: 27px; letter-spacing: 0.5px; color: var(--grey-text); line-height: 34px;
  }
  .person-title { font-size: 15px; color: var(--orange); line-height: 20px; }
  .person-phone {
    font-size: 17px; color: var(--accent-blue); margin-top: 24px; line-height: 22px;
  }
  .person-email { font-size: 15px; color: var(--grey-dark); line-height: 22px; }
</style>
</head>
<body>

<section class="card card--front" aria-label="Card front">
  <div class="front-backdrop" role="img" aria-label="Soft blue bokeh light background"></div>
  <div class="front-brand">
    <span class="brand-dot"></span>
    <span class="brand-name">Trelvan Media</span>
  </div>
  <address class="front-contact">
    Toll Free: 866-381-7459<br>
    4315 W. Calloway Ave.<br>
    Ste. 140, Tucson, AZ 85792
  </address>
  <div class="front-divider"></div>
  <ul class="front-social">
    <li><span class="social-mark"></span>@trelvanmedia</li>
    <li><span class="social-mark"></span>linkway.example/trelvanmedia</li>
    <li><span class="social-mark"></span>www.trelvanmedia.example</li>
  </ul>
</section>

<section class="card card--back" aria-label="Card back">
  <svg class="back-swoosh" width="492" height="278" viewBox="0 0 492 278" aria-hidden="true">
    <path d="M418 52 C330 70 230 130 222 200 C218 240 236 268 252 278 L240 278 C220 262 205 236 208 200 C216 120 320 66 418 52 Z" fill="var(--accent-blue)"/>
    <path d="M420 278 C450 270 475 260 492 245 L492 278 Z" fill="var(--accent-blue)"/>
  </svg>
  <div class="back-tab"></div>
  <div class="back-brand">
    <span class="brand-dot"></span>
    <span class="brand-name">Trelvan Media</span>
  </div>
  <div class="services">
    <p class="services-title"><span>Our</span> Services</p>
    <ul>
      <li><span class="service-dot"></span>Web Design</li>
      <li><span class="service-dot"></span>Internet Marketing</li>
      <li><span class="service-dot"></span>Website Management</li>
    </ul>
  </div>
  <div class="person">
    <p class="person-name">MARK LENNER</p>
    <p class="person-title">President/CEO</p>
    <p class="person-phone">520-381-7459</p>
    <p class="person-email">mark@trelvanmedia.example</p>
  </div>
</section>

</body>
</html>
```